Business Card: RW Office Partners - Your organised problem solver

Business Name: RW Office Partners
Website: www.rwofficepartners.com.au
Email: marisol@rwofficepartners.com.au
Mobile: 61 482 907 236
Facebook: @rwofficepartners
Instrgram: @rwofficepartners

Brading Colours:
HEX
#986474
#ddccd3
#7a8498
#c9d8e4
#000000
#ffffff

Tag Line: Your organised problem solver

Link to DRAFT website:
https://deskhelpcollective.wixsite.com/rw-office-partners

About Page from the website:
My name is Marisol Wrenfield, and I would love to assist you to become more productive in your day to day and achieve your business and personal goals.
My mission is to give you time, time to work on the important tasks of your business or to be able to spend more time with your family. I will take on the tasks you don’t have time for, don’t know well or simply don’t like to do.
I have an extensive background in Administration, Tender Coordination, Document Control, WHS and Quality Management working primarily in the Construction, Mining and Corporate World.
I am passionate about being organised, having order and making things in your life (and mine) easier! I love to watch something unfold and grow into something amazing! I am known for being the go-to problem solver, the organiser of all things, producing high standards of work even under pressure. I’m also a confident communicator, and I understand that you’re busy running your business.

Target Market(s)

Small to Medium Business who require assistance in their business by a virtual assistant.

Industry/Entity Type

Virtual Assistant

Contact Information for Business Card

Mobile: 61 482 907 236

Font styles to use
Sans Serif

Colors
ffffff

Requirements
Must have
• Branding Colours as outlined.
Contact Details as outlined.
Logo as provided.
Proper contact details - mobile, facebook, instragm, website.
Simple, Elegant, very clean looking.
Should not have
• Note cute with pictures.
Not too girly as still want to market to construction companies.

```html
<!DOCTYPE html>
<html lang="en">
<head>
<meta charset="utf-8">
<title>RW Office Partners – Business Card</title>
<link href="https://fonts.googleapis.com/css2?family=Arimo:wght@400&family=Lato:wght@400;700&display=swap" rel="stylesheet">
<style>
  :root {
    --mauve: #986474;
    --mauve-light: #ddccd3;
    --slate: #7a8498;
    --mist: #c9d8e4;
    --black: #000000;
    --ink: #0b0b0b;
    --white: #ffffff;
    --backdrop: #3a3a3c;
    --rule: #9a9a9a;
    --text: #1d1d1d;
  }
  * { box-sizing: border-box; margin: 0; padding: 0; }
  html, body { width: 1200px; height: 1200px; overflow: hidden; }
  body {
    background: var(--backdrop);
    display: flex;
    flex-direction: column;
    align-items: center;
    justify-content: center;
    gap: 60px;
  }
  .card {
    width: 700px;
    height: 400px;
    border-radius: 90px 6px 90px 6px;
    position: relative;
    overflow: hidden;
  }
  .card--front {
    background: var(--ink);
    display: flex;
    flex-direction: column;
    align-items: center;
    justify-content: center;
    gap: 34px;
  }
  .brand-name {
    font-family: "Lato", sans-serif;
    font-weight: 700;
    color: var(--mauve);
    letter-spacing: 1px;
  }
  .card--front .brand-name { font-size: 46px; }
  .tagline {
    font-family: "Arimo", sans-serif;
    font-size: 24px;
    color: var(--white);
    letter-spacing: 0.5px;
  }
  .card--back {
    background: var(--white);
    display: flex;
    align-items: center;
    padding: 0 40px 0 50px;
  }
  .card--back .brand-name {
    font-size: 46px;
    line-height: 1.05;
    width: 230px;
  }
  .divider {
    width: 2px;
    height: 170px;
    background: var(--rule);
    margin: 0 26px 0 20px;
    flex: none;
  }
  .contact-list {
    list-style: none;
    font-family: "Lato", sans-serif;
    font-size: 20px;
    color: var(--text);
  }
  .contact-list li {
    display: flex;
    align-items: center;
    gap: 10px;
    line-height: 1.45;
    white-space: nowrap;
  }
  .contact-list .icon { width: 18px; height: 18px; flex: none; }
  .contact-list .social-gap { margin-top: 16px; }
  .social-dot {
    width: 22px; height: 22px;
    border: 1.5px solid var(--slate);
    border-radius: 50%;
    flex: none;
  }
</style>
</head>
<body>

<section class="card card--front" aria-label="Card front">
  <div class="brand-name">RW Office Partners</div>
  <p class="tagline">Your organised problem solver</p>
</section>

<section class="card card--back" aria-label="Card back">
  <div class="brand-name">RW Office Partners</div>
  <span class="divider"></span>
  <ul class="contact-list">
    <li>
      <svg class="icon" viewBox="0 0 24 24" aria-hidden="true"><path fill="#986474" d="M3 9c0-3 4-5 9-5s9 2 9 5v2h-5V9c-1-.6-2.4-1-4-1s-3 .4-4 1v2H3zM6 13h12l2 7H4z"/></svg>
      61 482 907 236
    </li>
    <li>
      <svg class="icon" viewBox="0 0 24 24" aria-hidden="true"><rect x="2" y="5" width="20" height="14" fill="#986474"/><path d="M2 5l10 8 10-8" stroke="#fff" stroke-width="1.8" fill="none"/></svg>
      marisol@rwofficepartners.com.au
    </li>
    <li>
      <svg class="icon" viewBox="0 0 24 24" aria-hidden="true"><circle cx="12" cy="12" r="10" fill="#986474"/><path d="M2 12h20M12 2c3 3 3 17 0 20M12 2c-3 3-3 17 0 20" stroke="#fff" stroke-width="1.2" fill="none"/></svg>
      www.rwofficepartners.com.au
    </li>
    <li class="social-gap">
      <span class="social-dot"></span>
      @rwofficepartners
    </li>
    <li>
      <span class="social-dot"></span>
      @rwofficepartners
    </li>
  </ul>
</section>

</body>
</html>
```